75%-100% OFF - Insulation Banner Design

Need banners created for an online marketing push for my insulation business Tivoran Energy.

www.tivoranenergy.com

Specifically - I would like the banners to pop utilizing our colors in neon. To see samples of colors we use - visit our asset folder.

https://files.quelmarsh.net/share/7kXpw20LmzQaRt5vYbNe83HsUd4cJf?view=open

I will attach sample files to this project.

The banner must highlight 75%-100% off Insulation and Weatherization. If you can include our current perfect Ratewell somewhere in the advertisement that would be awesome but not a requirement.

The banner must meet Hearthwise logo guidelines. Please see attachment.

Target Market(s)

Home Owners

Industry/Entity Type

Insulation and Construction

Font styles to use
Sans Serif

Colors
59FF00
82FF00
B8FF75
E3FFCB
F4FFEA

Requirements
Must have
• Hearthwise Logo per project description. Must have 75-100% off somewhere that is very clear. And must have our company Tivoran Energy Logo.
Nice to have
• Tivoran Energy Logo

```html
<!DOCTYPE html>
<html lang="en">
<head>
<meta charset="utf-8">
<title>Tivoran Energy – Insulation Banners</title>
<link rel="stylesheet" href="https://fonts.googleapis.com/css2?family=Montserrat:wght@500;600;700;800&display=swap">
<style>
  :root{
    --board:#a6a6a6;
    --neon:#59ff00;
    --neon-2:#82ff00;
    --neon-soft:#b8ff75;
    --pink:#ff5cef;
    --pink-glow:#ff00dd;
    --ink:#1d1d1d;
    --navy:#1f4a74;
    --white:#ffffff;
    --forest:#1e5a12;
    --forest-deep:#0f3d0a;
    --shade:rgba(70,70,70,.55);
    --divider:#cfcfcf;
  }
  *{margin:0;padding:0;box-sizing:border-box}
  html,body{width:697px;height:1200px;overflow:hidden}
  body{background:var(--board);font-family:"Montserrat",Arial,sans-serif;position:relative}

  .banner{position:absolute;left:61px;width:574px;height:328px;overflow:hidden;background:var(--white)}
  .banner--cozy{top:51px}
  .banner--attic{top:428px}
  .banner--services{top:805px}

  .layer{position:absolute}
  .fill{position:absolute;inset:0}

  .brand{position:absolute;display:flex;align-items:center;gap:5px;font-weight:600;font-size:13px;letter-spacing:.2px;white-space:nowrap}
  .brand__mark{width:9px;height:9px;background:currentColor}
  .brand--navy{color:var(--navy)}
  .brand--light{color:var(--white)}

  .headline{position:absolute;font-weight:800;text-transform:uppercase;font-size:20.5px;line-height:26.7px;letter-spacing:-.3px;white-space:nowrap}
  .headline--small{font-size:16.5px}
  .headline--pink{color:#ffe6fc;text-shadow:0 0 2px var(--pink),0 0 4px var(--pink-glow),0 0 8px var(--pink-glow),0 0 12px var(--pink)}
  .headline--green{color:var(--neon-soft);text-shadow:0 0 2px var(--neon),0 0 5px var(--neon),0 0 10px var(--neon-2)}

  .offer{position:absolute;font-weight:800;text-transform:uppercase;white-space:nowrap;letter-spacing:-.2px}
  .offer--on-light{color:var(--forest);font-size:15px;line-height:18px}
  .offer--on-photo{color:var(--neon-soft);font-size:21px;line-height:24px;text-shadow:0 0 3px var(--forest-deep),0 0 6px var(--forest-deep),0 0 10px var(--neon)}
  .offer__small{display:block;font-size:9px;line-height:12px;font-weight:700;color:var(--ink);letter-spacing:.2px}

  .call{position:absolute;display:flex;align-items:center;gap:8px}
  .call__badge{width:41px;height:41px;border-radius:50%;background:var(--neon);border:2px solid var(--white);box-shadow:0 0 0 2px var(--neon);display:flex;align-items:center;justify-content:center;flex:none}
  .call__badge--outline{width:32px;height:32px;background:none;border:1.5px solid var(--ink);box-shadow:none}
  .call__label{font-size:8px;font-weight:600;color:var(--ink)}
  .call__number{font-size:14.5px;font-weight:700;color:var(--ink);line-height:1.25;letter-spacing:.2px;white-space:nowrap}

  .partners{position:absolute;display:flex;align-items:center}
  .partner{font-weight:700;font-size:9px;color:#4a2a14;white-space:nowrap}
  .partner--rating{font-size:14px;font-weight:600;color:#3a6fd8}
  .partners__divider{width:1px;height:33px;background:var(--divider);margin:0 14px}

  .shade-box{position:absolute;background:var(--shade)}
  .shade-box__bar{position:absolute;right:0;top:4px;bottom:4px;width:2.5px;background:var(--neon)}
  .shape{position:absolute;left:0;top:0}
</style>
</head>
<body>

<!-- Banner 1: cozy house -->
<section class="banner banner--cozy">
  <div class="layer" style="left:0;top:0;width:574px;height:196px;background:linear-gradient(160deg,#cfeefb 0%,#9fdcf5 45%,#c9ecfa 100%)" role="img" aria-label="Soft blue winter sky"></div>
  <div class="layer" style="left:300px;top:40px;width:274px;height:270px;border-radius:40% 10% 30% 40%;background:radial-gradient(ellipse at 55% 30%,#3b74b0 0%,#b88a5a 32%,#b9bcbf 58%,rgba(200,202,205,0) 76%)" role="img" aria-label="Toy house with blue roof wrapped in a grey knitted scarf"></div>

  <div class="brand brand--navy" style="left:31px;top:24px">
    <span class="brand__mark"></span>Tivoran Energy
  </div>

  <h1 class="headline headline--pink" style="left:29px;top:66px">
    We can help you save<br>on your energy bills by<br>improving your energy<br>efficiency
  </h1>

  <div class="call" style="left:31px;top:203px">
    <span class="call__badge">
      <svg width="18" height="18" viewBox="0 0 24 24"><path fill="#fff" d="M6.6 10.8a15.1 15.1 0 0 0 6.6 6.6l2.2-2.2c.3-.3.7-.4 1-.2 1.1.4 2.3.6 3.6.6.6 0 1 .4 1 1V20c0 .6-.4 1-1 1C10.6 21 3 13.4 3 4c0-.6.4-1 1-1h3.5c.6 0 1 .4 1 1 0 1.3.2 2.5.6 3.6.1.3 0 .7-.2 1z"/></svg>
    </span>
    <div>
      <p class="call__label">Call us Today :</p>
      <p class="call__number">555-214-3870</p>
    </div>
  </div>

  <p class="offer offer--on-light" style="left:194px;top:210px">
    75%–100% OFF
    <span class="offer__small">Insulation &amp; Weatherization</span>
  </p>

  <div class="layer" style="left:24px;top:254px;width:207px;height:74px;border-radius:6px;background:linear-gradient(90deg,#e9f3ec 0%,#36a65a 40%,#f2f4f3 70%,#dcdcdc 100%)" role="img" aria-label="Company box truck, van and pickup"></div>

  <div class="partners" style="left:245px;top:290px">
    <span class="partner">Hearthwise</span>
    <span class="partners__divider"></span>
    <span class="partner partner--rating">Ratewell</span>
  </div>
</section>

<!-- Banner 2: attic -->
<section class="banner banner--attic">
  <div class="fill" style="background:linear-gradient(135deg,#d8c8a2 0%,#b99c66 40%,#c8b088 65%,#8f6a3c 100%)" role="img" aria-label="Attic interior with insulation between rafters, skylight and ladder"></div>

  <div class="brand brand--light" style="left:35px;top:14px;font-size:16px">
    <span class="brand__mark"></span>Tivoran Energy
  </div>

  <div class="shade-box" style="left:29px;top:58px;width:345px;height:130px">
    <span class="shade-box__bar"></span>
  </div>
  <h1 class="headline headline--green" style="left:46px;top:69px">
    We can help you save<br>on your energy bills by<br>improving your energy<br>efficiency
  </h1>

  <p class="offer offer--on-photo" style="left:46px;top:200px">75%–100% OFF Insulation</p>

  <svg class="shape" width="574" height="328" viewBox="0 0 574 328">
    <polygon points="243,276 415,276 391,328 222,328" fill="var(--neon)"/>
    <polygon points="415,276 574,276 574,328 391,328" fill="var(--white)"/>
  </svg>

  <div class="layer" style="left:5px;top:258px;width:233px;height:69px;border-radius:6px;background:linear-gradient(90deg,#eef3ef 0%,#2f9e55 35%,#f1f4f2 60%,#2fa356 80%,#eceeed 100%)" role="img" aria-label="Company box truck and van"></div>

  <div class="call" style="left:247px;top:285px">
    <span class="call__badge call__badge--outline">
      <svg width="15" height="15" viewBox="0 0 24 24"><path fill="var(--ink)" d="M6.6 10.8a15.1 15.1 0 0 0 6.6 6.6l2.2-2.2c.3-.3.7-.4 1-.2 1.1.4 2.3.6 3.6.6.6 0 1 .4 1 1V20c0 .6-.4 1-1 1C10.6 21 3 13.4 3 4c0-.6.4-1 1-1h3.5c.6 0 1 .4 1 1 0 1.3.2 2.5.6 3.6.1.3 0 .7-.2 1z"/></svg>
    </span>
    <div>
      <p class="call__label">Call us Today :</p>
      <p class="call__number">555-214-3870</p>
    </div>
  </div>

  <div class="partners" style="left:414px;top:286px">
    <span class="partner">Hearthwise</span>
    <span class="partners__divider" style="margin:0 12px"></span>
    <span class="partner partner--rating">Ratewell</span>
  </div>
</section>

<!-- Banner 3: services -->
<section class="banner banner--services">
  <div class="fill" style="background:linear-gradient(125deg,#e6dccb 0%,#cbb98f 30%,#a99a5c 55%,#c3a56d 75%,#8c6a38 100%)" role="img" aria-label="Attic under construction with mineral wool insulation and skylight"></div>

  <div class="brand brand--light" style="left:31px;top:22px">
    <span class="brand__mark"></span>Tivoran Energy
  </div>

  <svg class="shape" width="574" height="328" viewBox="0 0 574 328">
    <defs>
      <linearGradient id="forestFade" x1="0" y1="0" x2="1" y2="0">
        <stop offset="0" stop-color="#0f3d0a"/>
        <stop offset="1" stop-color="#1e5a12"/>
      </linearGradient>
    </defs>
    <polygon points="0,222 210,222 255,328 0,328" fill="url(#forestFade)"/>
    <polygon points="377,222 574,222 574,328 334,328" fill="var(--white)"/>
  </svg>

  <p class="offer offer--on-photo" style="left:32px;top:188px">75%–100% OFF</p>

  <h2 class="headline headline--green headline--small" style="left:32px;top:236px">
    Insulation and<br>weatherization<br>energy savings
  </h2>

  <div class="call" style="left:394px;top:234px">
    <span class="call__badge">
      <svg width="18" height="18" viewBox="0 0 24 24"><path fill="#fff" d="M6.6 10.8a15.1 15.1 0 0 0 6.6 6.6l2.2-2.2c.3-.3.7-.4 1-.2 1.1.4 2.3.6 3.6.6.6 0 1 .4 1 1V20c0 .6-.4 1-1 1C10.6 21 3 13.4 3 4c0-.6.4-1 1-1h3.5c.6 0 1 .4 1 1 0 1.3.2 2.5.6 3.6.1.3 0 .7-.2 1z"/></svg>
    </span>
    <div>
      <p class="call__label">Call us Today :</p>
      <p class="call__number">555-214-3870</p>
    </div>
  </div>

  <div class="partners" style="left:389px;top:283px">
    <span class="partner">Hearthwise</span>
    <span class="partners__divider" style="margin:0 12px"></span>
    <span class="partner partner--rating">Ratewell</span>
  </div>
</section>

</body>
</html>
```